Simple Recipe eBook

I need the graphic work done for a simple recipe ebook, I have attached all of the required information for it, as well as our company logo. Further company info can be found at velorabix.com

I would like each recipe page to include 2 recipes, each recipe needs to include ingredients, picture, method, and nutritional info.

I would like the style to appear fresh and healthy, with lots of graphics and colours to match.
Please let me know if you need any guidance

Target Market(s)

Females aged from 15-25

Industry/Entity Type

It Company

```html
<!DOCTYPE html>
<html lang="en">
<head>
<meta charset="utf-8">
<title>Velorabix Detox Guide – Dos</title>
<link rel="stylesheet" href="https://fonts.googleapis.com/css2?family=Arvo:wght@700&family=Zilla+Slab:wght@400;500&family=Raleway:wght@400&family=Open+Sans:wght@700&display=swap">
<style>
  :root {
    --backdrop: #e6e6e6;
    --paper: #ffffff;
    --sky: #87c8f0;
    --teal: #13a39b;
    --blue: #0f6db6;
    --pale-blue: #8ccaee;
    --ink: #555555;
    --white: #ffffff;
  }
  html, body {
    margin: 0;
    width: 1200px;
    height: 1000px;
    overflow: hidden;
    background: var(--backdrop);
  }
  .spread {
    position: absolute;
    left: 90px;
    top: 156px;
    width: 1017px;
    height: 719px;
    display: flex;
  }
  .page-intro {
    position: relative;
    width: 508px;
    background: var(--paper);
  }
  .page-dos {
    position: relative;
    width: 509px;
    background: var(--sky);
    color: var(--white);
  }
  .intro-lead {
    position: absolute;
    left: 46px;
    top: 42px;
    margin: 0;
    font: 400 13px/19px "Raleway", sans-serif;
    color: var(--ink);
    letter-spacing: 0.3px;
  }
  .intro-mission {
    position: absolute;
    left: 46px;
    top: 80px;
    margin: 0;
    font: 400 17px/22px "Zilla Slab", serif;
    color: var(--teal);
    letter-spacing: 1.2px;
    text-transform: uppercase;
  }
  .intro-body {
    position: absolute;
    left: 46px;
    top: 139px;
    margin: 0;
    font: 400 13px/17px "Raleway", sans-serif;
    color: var(--ink);
    letter-spacing: 0.2px;
  }
  .intro-call {
    position: absolute;
    left: 44px;
    top: 172px;
    margin: 0;
    font: 700 46px/56px "Arvo", serif;
    color: var(--teal);
    white-space: nowrap;
  }
  .intro-call .call-small { font-size: 34px; }
  .habit-icons {
    position: absolute;
    left: 0;
    top: 0;
  }
  .goal-title {
    font: 700 24px "Open Sans", sans-serif;
    fill: var(--white);
  }
  .goal-line {
    font: 700 14px "Open Sans", sans-serif;
    fill: var(--white);
    letter-spacing: 1px;
  }
  .dos-title {
    position: absolute;
    left: 53px;
    top: 70px;
    margin: 0;
    font: 700 44px/52px "Arvo", serif;
    letter-spacing: 1px;
  }
  .dos-tick {
    position: absolute;
    right: 0;
    top: 74px;
  }
  .dos-list {
    position: absolute;
    left: 52px;
    top: 180px;
    width: 440px;
    margin: 0;
    padding: 0;
    list-style: none;
  }
  .dos-item { margin-bottom: 8px; }
  .dos-item h3 {
    margin: 0 0 2px;
    font: 500 13.5px/18px "Zilla Slab", serif;
    color: var(--blue);
    letter-spacing: 0.8px;
    text-transform: uppercase;
  }
  .dos-item p {
    margin: 0;
    font: 400 11px/14px "Raleway", sans-serif;
    color: var(--white);
  }
</style>
</head>
<body>
<main class="spread">
  <section class="page-intro">
    <p class="intro-lead">At Velorabix we want to help you be the best you can be!<br>That’s why we have put together this simple guide</p>
    <p class="intro-mission">To motivate, inspire, inform,<br>and help you reach your goals.</p>
    <p class="intro-body">Below you will find a collection of healthy and easy recipe ideas<br>and tips to kickstart your detox and diet journey.</p>
    <h1 class="intro-call">READY? <span class="call-small">SET....GO!</span></h1>

    <svg class="habit-icons" width="508" height="719" viewBox="0 0 508 719">
      <circle cx="181" cy="345" r="60" fill="var(--teal)" role="img" aria-label="Bicycle pictogram for exercise"/>
      <circle cx="326" cy="345" r="60" fill="var(--blue)" role="img" aria-label="Gauge pictogram for counting calories"/>
      <circle cx="117" cy="472" r="60" fill="var(--blue)"/>
      <circle cx="254" cy="472" r="60" fill="var(--pale-blue)"/>
      <circle cx="391" cy="472" r="60" fill="var(--teal)" role="img" aria-label="Glass and water bottles pictogram"/>
      <circle cx="181" cy="595" r="60" fill="var(--teal)" role="img" aria-label="Melon slice and carrot pictogram"/>
      <circle cx="326" cy="595" r="60" fill="var(--blue)" role="img" aria-label="Sleeping person in bed pictogram"/>
      <text class="goal-title" x="216" y="454">GOAL!</text>
      <text class="goal-line" x="215" y="478">1............</text>
      <text class="goal-line" x="215" y="496">2............</text>
      <text class="goal-line" x="215" y="514">3............</text>
    </svg>
  </section>

  <section class="page-dos">
    <h2 class="dos-title">DOS</h2>
    <svg class="dos-tick" width="62" height="52" viewBox="0 0 62 52" role="img" aria-label="Tick">
      <rect width="62" height="52" fill="var(--blue)"/>
      <path d="M17 28 L27 40 L46 10" fill="none" stroke="var(--white)" stroke-width="5" stroke-linecap="round" stroke-linejoin="round"/>
    </svg>
    <ul class="dos-list">
      <li class="dos-item"><h3>Exercise!</h3><p>Exercise is the key to achieving your goals. Aim for at least 30 minutes<br>of high intensity cardio or weight training each day</p></li>
      <li class="dos-item"><h3>Count your calories!</h3><p>To be sure you aren’t eating too much you should make sure to count your calories.<br>Download an app like FitLedger to help you keep track on the go.<br>The app will also help decide how many calories you should be consuming per day.</p></li>
      <li class="dos-item"><h3>Drink plenty of water!</h3><p>Staying hydrated is important to keep your body functioning at its peak.<br>A glass of water before each meal can help you feel fuller quicker.<br>It also helps flush nasty toxins.</p></li>
      <li class="dos-item"><h3>Get a goodnight sleep!</h3><p>Your beauty rest is important to help your body repair.<br>6-8 hours every night is recommended.</p></li>
      <li class="dos-item"><h3>Write down your goals!</h3><p>Did you know that writing down your goals increases your chance of actually<br>completing them? It does! Give it a go. Write them down and stick to them.<br>Hard work and consistency pays off!</p></li>
      <li class="dos-item"><h3>Eat fruit &amp; veggies!</h3><p>Fresh fruit and veges are loaded with healthy vitamins and antioxidants<br>that your body loves!</p></li>
      <li class="dos-item"><h3>Do it with a friend!</h3><p>Doing your diet and detox with a friend can be a great way to boost motivation<br>and get results. Keep each other on track and share ideas.</p></li>
    </ul>
  </section>
</main>
</body>
</html>
```